Buch-Cover für Lichtblick gesucht
Zielgruppe
Wir sind eine Firma die hochwertige Fitnessprodukte produziert und vertreibt. Unsere Zielgruppe sind gesundheitsbewusste Frauen ab Mitte 20 bis open end, die hohe Ansprüche an sich selbst stellen und sich für das Thema Selbstoptimierung interessieren.
Aufgabenstellung
Es soll ein Hardcover gestaltet werden.
Buchtitel: Lichtblick, Untertitel: Ein Sommer voller Mut
Detaillierte Beschreibung der Projektanforderungen siehe Anhang Projektbeschreibung. Darüber hinaus bin ich auch für alternative Gestaltungs-Ideen offen.
Das Design soll der Käuferin folgendes vermitteln:
- Wertigkeit
- Positivität
und sie ein bisschen träumen lassen und natürlich neugierig auf den Inhalt machen.

```html
<!DOCTYPE html>
<html lang="de">
<head>
<meta charset="utf-8">
<title>Lichtblick – Buchumschlag</title>
<link rel="stylesheet" href="https://fonts.googleapis.com/css2?family=Cinzel:wght@400;700;900&family=EB+Garamond:wght@400;500&display=swap">
<style>
  :root {
    --spine-orange: #f5a32f;
    --ink: #231a17;
    --panel: rgba(236, 234, 240, 0.78);
    --gold-light: #ffe08a;
    --gold: #f0b43a;
    --gold-deep: #a8661a;
    --photo-dark: #3a2a1e;
    --photo-mid: #8a6540;
    --photo-light: #d9b77e;
    --white: #ffffff;
  }
  * { margin: 0; padding: 0; box-sizing: border-box; }
  html, body { width: 1200px; height: 894px; overflow: hidden; background: #fff; }
  .cover { position: relative; width: 1200px; height: 894px; overflow: hidden; font-family: "EB Garamond", serif; }

  .back-photo {
    position: absolute; left: 0; top: 0; width: 553px; height: 894px;
    background:
      radial-gradient(circle at 20% 85%, rgba(255,220,150,.55), transparent 35%),
      radial-gradient(circle at 85% 10%, rgba(255,230,180,.5), transparent 40%),
      linear-gradient(170deg, var(--photo-light) 0%, var(--photo-mid) 45%, var(--photo-dark) 100%);
  }
  .back-panel {
    position: absolute; left: 57px; top: 77px; width: 471px; height: 624px;
    background: var(--panel);
  }
  .back-heading {
    position: absolute; left: 57px; top: 110px; width: 471px; text-align: center;
    font-family: "Cinzel", serif; font-weight: 700; font-size: 37px; color: var(--ink);
    letter-spacing: 1px;
  }
  .back-blurb {
    position: absolute; left: 68px; top: 182px; width: 456px;
    font-size: 17.4px; line-height: 21.8px; color: var(--ink);
  }
  .back-blurb p + p { margin-top: 21.8px; }
  .barcode-area { position: absolute; left: 311px; top: 723px; width: 217px; height: 130px; background: var(--white); }

  .spine { position: absolute; left: 553px; top: 0; width: 90px; height: 894px; background: var(--spine-orange); }
  .spine-imprint {
    position: absolute; left: 0; top: 58px; width: 90px; text-align: center;
    font-family: "Cinzel", serif; font-weight: 700; font-size: 14px; color: var(--white); letter-spacing: 1px;
  }
  .spine-title, .spine-author {
    position: absolute; left: 45px; color: var(--white); font-family: "Cinzel", serif;
    transform-origin: 0 0; transform: rotate(90deg); white-space: nowrap;
  }
  .spine-title { top: 255px; margin-left: 24px; font-size: 44px; font-weight: 400; letter-spacing: 1px; }
  .spine-author { top: 688px; margin-left: 11px; font-size: 16px; font-weight: 700; letter-spacing: 1px; }

  .front-photo {
    position: absolute; left: 643px; top: 0; width: 557px; height: 894px;
    background:
      radial-gradient(ellipse at 45% 55%, rgba(230,190,120,.55), transparent 45%),
      radial-gradient(circle at 95% 40%, rgba(245,220,170,.6), transparent 30%),
      linear-gradient(180deg, #6f5a4a 0%, var(--photo-mid) 40%, var(--photo-dark) 75%, #2a1d14 100%);
  }
  .front-author {
    position: absolute; left: 643px; top: 42px; width: 557px; text-align: center;
    font-family: "Cinzel", serif; font-weight: 700; font-size: 20px; color: var(--ink); letter-spacing: 1px;
  }
  .gold {
    font-family: "Cinzel", serif; font-weight: 900; position: absolute; text-align: center;
    background: linear-gradient(180deg, var(--gold-light) 0%, var(--gold) 50%, var(--gold-deep) 100%);
    -webkit-background-clip: text; background-clip: text; color: transparent;
    filter: drop-shadow(1px 2px 2px rgba(40,20,0,.6));
  }
  .front-title { left: 643px; top: 52px; width: 557px; font-size: 78px; letter-spacing: 1px; }
  .front-subtitle-1 { left: 643px; top: 692px; width: 557px; font-size: 62px; }
  .front-subtitle-2 { left: 643px; top: 788px; width: 557px; font-size: 56px; }
</style>
</head>
<body>
<div class="cover">
  <div class="back-photo" role="img" aria-label="Unscharfes, warm leuchtendes Bokeh-Foto aus dem Autoinneren"></div>
  <div class="back-panel"></div>
  <h2 class="back-heading">Was zählt wirklich?</h2>
  <div class="back-blurb">
    <p>Ich habe mich oft gefragt: Wie soll ich bloß die Liebe und Bestätigung, die mir damals in meiner Kindheit verwehrt blieben, „nachholen“? Lösungsansätze für mein Problem hatte ich in der Vergangenheit durchaus: Ich versuchte das Loch in mir mit Hilfe zur Selbsthilfe, Erfolg im Job und Konsum zu stopfen. Und meine Partner mussten auch für so einiges herhalten.</p>
    <p>Von Gott wollte ich lange nichts wissen. Schließlich hatte er es zugelassen, dass mir sehr viel Unheil in meinem Leben widerfahren ist. Und deshalb war ich echt wütend auf ihn.</p>
    <p>Heutzutage bin ich mir sicher, dass ich mit dieser Denkweise meine Lebenszeit verschwendet habe. Letzten Sommer begriff ich endlich: im Leben gilt die gleiche Gesetzmäßigkeit wie beim Autofahren. Der Rückspiegel ist so klein und die Frontscheibe so groß, weil das, was vor uns liegt, viel wichtiger ist als das, was hinter uns liegt. Aufgrund dieser Erkenntnis entschied ich mich, einen völlig neuen Weg einzuschlagen und wagte mich auf eine spannende Reise, die mein Leben für immer veränderte …</p>
  </div>
  <div class="barcode-area"></div>

  <div class="spine">
    <div class="spine-imprint">Solvia</div>
  </div>
  <div class="spine-title">Lichtblick</div>
  <div class="spine-author">Marte Quisselt</div>

  <div class="front-photo" role="img" aria-label="Frau mit Sonnenbrille am Steuer eines Cabrios, Blick auf eine sonnige Landstraße"></div>
  <div class="front-author">Marte Quisselt</div>
  <h1 class="gold front-title">Lichtblick</h1>
  <div class="gold front-subtitle-1">Ein Sommer</div>
  <div class="gold front-subtitle-2">voller Mut</div>
</div>
</body>
</html>
```